Im want a website LIKE VRX's and FleetHollow.com's with product payment options like Trenzo's

I need a website LIKE VRX with a header made EXACTLY LIKE THAT OF FLEETHOLLOWS .

The front page photo should be like that of FLEETHOLLOW's webpage as well.

The name of the website will be called "M.K. (Caldera Key)".

We will be targeting ALL MARKETS in a small town in central Panama and charging businesses "listing fees" like a phone book does but also providing informational blogs, news, and other interesting activities.

THIS IS A MULTI PAGE WEBSITE

THIS IS WHERE VRX's website meets Brivelle/FleetHollow.

Once the layout is built I will tweak and modify, add information, and upload items for sale.

Here is a list of specific categories that should be listed out above the front page header image/search bar

-- Home -- News -- Travel -- Activities -- Shop & Dine -- Store -- More... --

These categories should be spread across the bottom of the page in three sections:

WHATS SO GREAT ABOUT (Caldera Key),
HAND PICKED TOURS
ACTIVITIES etc.

Also lets use www.Trenzo.example 's
"HOT DESTINATIONS"
"BEAT THE BEST PRICES IN BOQUETE"
"OCTOBERS INSIDER PICKS"
"TOP DESTINATIONS"
and spread them in four sections side-by-side near the bottom of the page.

Overall I would like to see the finished product to be something LIKE VRX's and FleetHollows.

WE NEED ONLINE PAYMENT OPTIONS LIKE BRIVELLE'S WEBSITE HAS

This will be a desktop website but should be very mobile friendly as well.

-rodmund

P.S. Good luck!

If it isn't already too late to change the website name, the name of the website should be "Caldera Key". Added Friday, October 9, 2015

What do you guys think the budget should be to win this? Added Saturday, October 10, 2015

www.palmorra.example is the most amazing simple site. Whoever can make me a replica with my specifications will win immediately!!!! Added Sunday, October 18, 2015

OMG www.palmorra.example is the bomb!So simple and elegant. Whoever can make me an EXACT REPLICA OF WWW.PALMORRA.EXAMPLE as my site with the specifications mentioned in my brief will take home the $825.00 immediately! Good luck amigos! Added Sunday, October 18, 2015

Does anybody know how to add recurring monthly billing options on this website? Added Sunday, October 18, 2015

ALL MARKETS

Product

Coded - Design and coding required

5+ page

• Coinvey payment options.
• I must be able to add and remove photos/text and video from the HTML files in the page.
• Be creative my friends, and may the odds be forever in your favor!
• I added some photos of a good layout for our page below.

```html
<!DOCTYPE html>
<html lang="en">
<head>
<meta charset="utf-8">
<title>Caldera Key</title>
<link rel="stylesheet" href="https://fonts.googleapis.com/css2?family=Cinzel:wght@400;700&family=Open+Sans:wght@400;600;700&display=swap">
<style>
:root{
  --navy:#0c2f6b;
  --blue:#1450a3;
  --bright:#1f6fd1;
  --topbar:#0a2658;
  --page:#eef1f5;
  --ink:#2b2f36;
  --muted:#7b8290;
  --line:#dde2ea;
  --red:#c8382b;
  --gold:#f2b01e;
  --white:#ffffff;
}
*{box-sizing:border-box;margin:0;padding:0}
html,body{width:1200px;height:2204px;overflow:hidden}
body{font-family:"Open Sans",Arial,sans-serif;color:var(--ink);background:var(--page);position:relative}
.side-scene{position:absolute;left:0;top:0;width:110px;height:1160px;background:linear-gradient(180deg,#9fc7e8 0%,#5f8c6a 45%,#d7c9a3 75%,var(--page) 100%)}
.side-scene.right{left:auto;right:0;width:100px;background:linear-gradient(180deg,#c6dcef 0%,#e4ecf3 60%,var(--page) 100%)}
.site{position:absolute;left:104px;top:0;width:992px;background:var(--white);box-shadow:0 0 18px rgba(0,0,0,.12)}
.topbar{height:32px;background:var(--topbar);color:#cfd9ec;font-size:11px;display:flex;align-items:center;justify-content:space-between;padding:0 22px}
.topbar span{margin-right:18px}
.topbar .right span{margin:0 0 0 18px}
.masthead{height:120px;display:flex;align-items:center;justify-content:space-between;padding:0 40px}
.brand{font-family:"Cinzel",Georgia,serif;font-size:34px;font-weight:700;color:var(--navy);letter-spacing:1px}
.contact-block{display:flex;align-items:center;gap:14px}
.contact-block .icon{width:40px;height:40px;border-radius:50%;border:2px solid var(--blue);display:flex;align-items:center;justify-content:center}
.contact-block .ph{font-weight:700;color:var(--navy);font-size:15px}
.contact-block .mail{font-size:11px;color:var(--muted)}
.btn{display:inline-block;background:var(--blue);color:var(--white);font-size:13px;font-weight:600;padding:9px 26px;border-radius:3px}
.login{margin-left:60px}
.mainnav{height:48px;background:var(--navy);display:flex;justify-content:space-around;align-items:center;color:var(--white);font-size:13px;padding:0 20px}
.hero{position:relative;height:400px;background:linear-gradient(180deg,#122a55 0%,#2c4f86 40%,#d39a4e 62%,#1b3660 80%,#0d1f3f 100%)}
.hero h2{position:absolute;left:36px;bottom:40px;font-family:"Cinzel",Georgia,serif;font-weight:400;color:var(--white);font-size:27px;line-height:1.25}
.hero .arrow{position:absolute;top:180px;width:30px;height:40px;background:rgba(0,0,0,.35);display:flex;align-items:center;justify-content:center}
.hero .arrow.l{left:0}.hero .arrow.r{right:0}
.welcome{text-align:center;padding:44px 150px 48px;border-bottom:1px solid var(--line)}
.section-title{font-family:"Cinzel",Georgia,serif;color:var(--navy);font-size:30px;font-weight:700;letter-spacing:1px}
.welcome p{font-size:12px;line-height:20px;color:var(--muted);margin:16px 0 26px}
.services{padding:46px 36px 30px;text-align:center}
.services .sub{font-size:12px;color:var(--muted);margin:6px 0 28px}
.cards{display:flex;gap:24px;text-align:left}
.card{flex:1}
.card .photo{position:relative;height:180px}
.card .price{position:absolute;right:10px;top:10px;background:var(--blue);color:var(--white);font-size:12px;font-weight:700;padding:6px 10px}
.card h3{font-family:"Cinzel",Georgia,serif;color:var(--navy);font-size:17px;margin:16px 0 8px}
.card p{font-size:11px;line-height:18px;color:var(--muted)}
.card .meta{display:flex;justify-content:space-between;font-size:11px;margin-top:10px}
.stars{color:var(--gold);letter-spacing:2px}
.card .more{display:block;color:var(--red);font-size:11px;font-weight:700;margin-top:8px}
.lower{display:flex;gap:40px;padding:30px 36px 40px}
.lower h4{font-family:"Cinzel",Georgia,serif;color:var(--navy);font-size:20px;margin-bottom:22px}
.news,.clients{flex:1}
.news-item{display:flex;gap:18px;margin-bottom:24px}
.news-item .thumb{width:140px;height:90px;flex:none}
.news-item h5{font-size:10px;color:var(--muted);font-weight:600}
.news-item .date{font-size:12px;color:var(--red);font-weight:700;margin:6px 0}
.news-item p{font-size:11px;line-height:17px;color:var(--muted)}
.quote{background:#f3f5f8;border:1px solid var(--line);padding:26px 28px 26px 56px;position:relative;font-size:11px;line-height:19px;color:var(--muted)}
.quote .mark{position:absolute;left:20px;top:14px;font-family:Georgia,serif;font-size:44px;color:#c3cad6}
.author{display:flex;align-items:center;gap:14px;margin-top:18px;padding-left:20px}
.author .avatar{width:50px;height:50px;border-radius:50%;background:linear-gradient(135deg,#d9b89a,#8a6c58)}
.author b{color:var(--red);font-size:12px}
.author span{font-size:11px;color:var(--muted)}
.footer{background:var(--navy);color:#d3dcee;display:flex;gap:30px;padding:34px 40px;height:248px;font-size:11px}
.footer h6{font-family:"Cinzel",Georgia,serif;color:var(--white);font-size:16px;font-weight:400;margin-bottom:16px}
.f-about{width:170px;text-align:center}
.f-about .badge{width:56px;height:56px;border-radius:50%;border:2px solid var(--white);background:var(--bright);margin:0 auto 12px}
.f-about p{line-height:17px}
.f-about .btn{margin-top:12px;font-size:11px;padding:7px 14px;background:var(--bright)}
.f-contact{width:220px}
.f-contact li{list-style:none;display:flex;gap:8px;align-items:center;margin-bottom:10px}
.f-news{flex:1}
.field{height:30px;background:var(--white);border-radius:2px;margin-bottom:10px;color:#8c93a0;padding:8px 10px}
.f-news .btn{background:var(--bright);font-size:11px;width:100%;text-align:center}
.f-social{width:150px}
.f-social li{list-style:none;display:flex;gap:8px;align-items:center;margin-bottom:9px}
.f-social i{width:12px;height:12px;background:#6e8fc7;display:block}
.copyright{height:44px;background:var(--topbar);color:#9fb0cf;font-size:10px;display:flex;align-items:center;justify-content:center}
</style>
</head>
<body>
<div class="side-scene" role="img" aria-label="Tropical beach with palm trees"></div>
<div class="side-scene right" role="img" aria-label="Soft sky and sea backdrop"></div>

<div class="site">
  <div class="topbar">
    <div><span>USD $ ▾</span><span>English ▾</span></div>
    <div class="right"><span>Help</span><span>Login</span></div>
  </div>

  <header class="masthead">
    <div class="brand">Caldera Key</div>
    <div class="contact-block">
      <div class="icon">
        <svg width="18" height="18" viewBox="0 0 24 24"><path fill="#1450a3" d="M6.6 10.8a15 15 0 0 0 6.6 6.6l2.2-2.2c.3-.3.7-.4 1-.2 1.1.4 2.3.6 3.6.6.6 0 1 .4 1 1V20c0 .6-.4 1-1 1A17 17 0 0 1 3 4c0-.6.4-1 1-1h3.5c.6 0 1 .4 1 1 0 1.3.2 2.5.6 3.6.1.3 0 .7-.2 1z"/></svg>
      </div>
      <div>
        <div class="ph">Ph: +908-555-0147</div>
        <div class="mail">hello@calderakey.example</div>
      </div>
      <a class="btn login">Login</a>
    </div>
  </header>

  <nav class="mainnav">
    <span>Home</span><span>About Us</span><span>Our Services</span><span>Blog</span><span>Portfolio</span><span>Contact Us</span>
  </nav>

  <section class="hero" role="img" aria-label="Coastal city skyline lit up at dusk">
    <div class="arrow l"><svg width="10" height="16" viewBox="0 0 10 16"><path d="M8 2 2 8l6 6" stroke="#fff" stroke-width="2" fill="none"/></svg></div>
    <div class="arrow r"><svg width="10" height="16" viewBox="0 0 10 16"><path d="m2 2 6 6-6 6" stroke="#fff" stroke-width="2" fill="none"/></svg></div>
    <h2>We will be targeting tourism<br>in central Panama</h2>
  </section>

  <section class="welcome">
    <h1 class="section-title">WELCOME TO CALDERA KEY</h1>
    <p>Caldera Key brings local listings, guides, news and events together for visitors and residents in the heart of central Panama. Browse trusted businesses, plan tours, book rooms and find rental vehicles in one place. Our team updates every page weekly so you always see what is open, new and worth a visit this season.</p>
    <a class="btn">View the Details</a>
  </section>

  <section class="services">
    <h2 class="section-title">OUR SERVICES</h2>
    <div class="sub">Our best specialized services</div>
    <div class="cards">
      <article class="card">
        <div class="photo" role="img" aria-label="Tour group on a city street at night" style="background:linear-gradient(160deg,#1d3f7a,#4f7cc0 55%,#0e2346)"><span class="price">$79.99</span></div>
        <h3>SELLING GUIDED TOURS</h3>
        <p>Explore waterfalls, coffee farms and cloud forest trails with a local guide who knows every path.</p>
        <div class="meta"><span class="stars">★★★★★</span><span>24 Reviews</span></div>
        <a class="more">CLICK HERE</a>
      </article>
      <article class="card">
        <div class="photo" role="img" aria-label="Hotel pool with palm trees at dusk" style="background:linear-gradient(170deg,#f1a35b,#8d5a8f 45%,#1f4b7a)"><span class="price">$79.99</span></div>
        <h3>HOTEL/HOSTELS</h3>
        <p>Compare rooms from cozy hostels to quiet valley lodges and book your stay in minutes.</p>
        <div class="meta"><span class="stars">★★★★★</span><span>24 Reviews</span></div>
        <a class="more">CLICK HERE</a>
      </article>
      <article class="card">
        <div class="photo" role="img" aria-label="Row of white rental cars" style="background:linear-gradient(165deg,#8fb3d9,#e6ebf1 55%,#6d7a8a)"><span class="price">$79.99</span></div>
        <h3>RENTAL VEHICLES</h3>
        <p>Pick up a car, scooter or jeep in town and drive the mountain roads at your own pace.</p>
        <div class="meta"><span class="stars">★★★★★</span><span>24 Reviews</span></div>
        <a class="more">CLICK HERE</a>
      </article>
    </div>
  </section>

  <section class="lower">
    <div class="news">
      <h4>OUR NEWS</h4>
      <div class="news-item">
        <div class="thumb" role="img" aria-label="Harbour skyline by day" style="background:linear-gradient(180deg,#9cc3e6,#3f6fa6)"></div>
        <div>
          <h5>SED UT PERSPICIATIS UNDE OMNIS</h5>
          <div class="date">15 - MARCH - 2015</div>
          <p>Fresh updates from the town market, new cafés and weekend events around the valley.</p>
        </div>
      </div>
      <div class="news-item">
        <div class="thumb" role="img" aria-label="City towers at sunset" style="background:linear-gradient(180deg,#e7b67a,#3d5680)"></div>
        <div>
          <h5>SED UT PERSPICIATIS UNDE OMNIS</h5>
          <div class="date">15 - MARCH - 2015</div>
          <p>New trail openings, festival dates and travel tips gathered by our local writers.</p>
        </div>
      </div>
    </div>
    <div class="clients">
      <h4>OUR HAPPIEST CLIENTS</h4>
      <blockquote class="quote">
        <span class="mark">“</span>
        We found a guide, a lodge and a rental car in one evening. Every listing was clear, prices were honest and the team answered our questions fast. The news pages helped us catch the flower fair and a coffee tasting we would have missed. We are already planning our next visit and will book everything here again.
      </blockquote>
      <div class="author">
        <div class="avatar" role="img" aria-label="Client portrait"></div>
        <div><b>Marla Quenby</b> <span>Valley Road, PA</span></div>
      </div>
    </div>
  </section>

  <footer class="footer">
    <div class="f-about">
      <div class="badge"></div>
      <p>Your local guide to tours, stays, dining and shops across the town and the green valley around it.</p>
      <a class="btn">Call to action</a>
    </div>
    <div class="f-contact">
      <h6>CONTACT US</h6>
      <ul>
        <li><svg width="12" height="14" viewBox="0 0 12 16"><path fill="#fff" d="M6 0a6 6 0 0 0-6 6c0 4.5 6 10 6 10s6-5.5 6-10a6 6 0 0 0-6-6zm0 8.5A2.5 2.5 0 1 1 6 3.5a2.5 2.5 0 0 1 0 5z"/></svg>24 Avenida Central, Central Panama</li>
        <li><svg width="12" height="12" viewBox="0 0 24 24"><path fill="#fff" d="M6.6 10.8a15 15 0 0 0 6.6 6.6l2.2-2.2c.3-.3.7-.4 1-.2 1.1.4 2.3.6 3.6.6.6 0 1 .4 1 1V20c0 .6-.4 1-1 1A17 17 0 0 1 3 4c0-.6.4-1 1-1h3.5c.6 0 1 .4 1 1 0 1.3.2 2.5.6 3.6.1.3 0 .7-.2 1z"/></svg>+908-555-0147</li>
        <li><svg width="12" height="10" viewBox="0 0 16 12"><rect x=".5" y=".5" width="15" height="11" fill="none" stroke="#fff"/><path d="m1 1 7 6 7-6" stroke="#fff" fill="none"/></svg>hello@calderakey.example</li>
      </ul>
    </div>
    <div class="f-news">
      <h6>SIGN UP FOR NEWSLETTER</h6>
      <div class="field">Enter Name</div>
      <div class="field">Email</div>
      <a class="btn">SIGN UP NOW</a>
    </div>
    <div class="f-social">
      <h6>SOCIAL MEDIA</h6>
      <ul>
        <li><i></i>Friendlane</li>
        <li><i></i>Chirpwire</li>
        <li><i></i>Circlepost</li>
        <li><i></i>Pinboardly</li>
      </ul>
    </div>
  </footer>
  <div class="copyright">© 2015 CalderaKey.example. All Rights Reserved.</div>
</div>
</body>
</html>
```